International Travel Technology R&D business needs a wordpress website

We are a start up team of initially 2 individuals but plan to grow our team quickly, we have deep experience in travel technology. Our goal is to provide next generation technology research and development on behalf of our clients who are leading players in the travel technology industry. Attached our logos.

Target Market(s)

Travel Technology companies

Industry/Entity Type

Travel Industry

Coding

Coded - Design and coding required

Font styles to use
Sans Serif

Requirements
Must have
• Make use of our logo and colour scheme in the attached. Has to have a sense of adventure/ stepping into the unknown but equally must convey a sense of professionalism , we are a safe pair of hands. Sample themes are in the attachment .
Nice to have
• We have identified a theme on skinharbor which we feel would be inspirational. We hahe attached them to help in the design as inspiration.
Should not have
• images of airplanes , hotels etc, we want to project a future image.

```html
<!DOCTYPE html>
<html lang="en">
<head>
<meta charset="utf-8">
<title>Vantage Trail Labs</title>
<link href="https://fonts.googleapis.com/css2?family=Open+Sans:wght@400;600;700&display=swap" rel="stylesheet">
<style>
:root{
  --green:#64a033;
  --blue:#5b9bd5;
  --navy:#1d2a4d;
  --text:#555;
  --muted:#999;
  --light:#f1f1f1;
  --card:#f4f4f4;
  --footer:#2b2b2b;
  --footer-deep:#1e1e1e;
  --white:#fff;
}
*{box-sizing:border-box;margin:0;padding:0}
html,body{width:1200px;height:2362px;overflow:hidden}
body{font-family:"Open Sans",Arial,sans-serif;color:var(--text);background:var(--white);position:relative}
.wrap{position:absolute;left:132px;width:936px}
section,header,footer{position:absolute;left:0;width:1200px}

/* header */
.site-header{top:0;height:145px}
.brand{position:absolute;left:132px;top:46px;display:flex;align-items:center;gap:12px}
.brand-dot{width:38px;height:38px;border-radius:50%;background:var(--blue)}
.brand-name{font-size:24px;font-weight:700;color:var(--navy);letter-spacing:1px}
.call{position:absolute;right:132px;top:32px;display:flex;align-items:center;gap:10px;text-align:right}
.call-label{font-size:13px;color:var(--muted);line-height:16px}
.call-number{font-size:18px;color:var(--blue);line-height:22px}
.call-icon{width:30px;height:30px;border-radius:50%;background:var(--blue);display:flex;align-items:center;justify-content:center}
.nav{position:absolute;right:132px;top:96px;display:flex;gap:30px;font-size:13px;color:var(--muted)}
.nav .active{color:var(--navy)}

/* hero */
.hero{top:145px;height:469px;background:linear-gradient(90deg,#8e8e8e 0%,#b5b5b5 45%,#9a9a9a 70%,#3a3a3a 100%)}
.hero-title{position:absolute;left:132px;top:176px;font-size:24px;font-weight:600;color:var(--white);line-height:32px}
.hero-arrow{position:absolute;top:218px;width:22px;height:32px;background:rgba(0,0,0,.35);display:flex;align-items:center;justify-content:center}
.hero-arrow.left{left:0}.hero-arrow.right{right:0}

/* welcome */
.welcome{top:614px;height:205px;text-align:center}
.section-title{font-size:24px;font-weight:600;color:var(--green)}
.welcome .section-title{margin-top:44px}
.welcome p{width:936px;margin:12px auto 0;font-size:11.5px;line-height:19px;color:var(--muted)}

/* services */
.services{top:819px;height:362px;background:var(--light);text-align:center}
.services .section-title{margin-top:38px}
.service-list{position:absolute;left:132px;width:936px;top:92px;display:flex;justify-content:space-between}
.service{width:290px}
.service-icon{width:72px;height:72px;border-radius:50%;background:var(--blue);margin:0 auto;display:flex;align-items:center;justify-content:center}
.service h3{font-size:20px;font-weight:600;color:var(--navy);margin-top:20px}
.service p{font-size:11.5px;line-height:19px;color:var(--muted);margin-top:10px;padding:0 14px}
.btn{display:inline-block;margin-top:20px;width:98px;height:32px;line-height:30px;border:1px solid #ccc;background:var(--white);font-size:11px;color:var(--text)}

/* projects */
.projects{top:1181px;height:422px}
.head-row{position:absolute;left:132px;width:936px;display:flex;justify-content:space-between;align-items:center}
.projects .head-row{top:44px}
.pager{display:flex;gap:4px}
.pager span{width:16px;height:16px;border-radius:50%;background:#ddd;display:flex;align-items:center;justify-content:center}
.pager span.on{background:#444}
.project-list{position:absolute;left:132px;top:93px;width:936px;display:flex;gap:2px}
.project{width:232.5px;background:var(--card);height:287px}
.project-img{height:159px}
.project h4{font-size:13px;font-weight:400;color:#222;line-height:19px;padding:16px 14px 0}
.project p{font-size:10px;line-height:15px;color:var(--muted);padding:8px 14px 0}
.more{color:var(--blue)}

/* news */
.news{top:1603px;height:240px;background:var(--light)}
.news .head-row{top:38px}
.view-all{background:#444;color:var(--white);font-size:9px;padding:3px 8px}
.news-list{position:absolute;left:132px;top:70px;width:936px;display:flex;justify-content:space-between}
.news-card{width:287px;height:143px;background:var(--white);display:flex}
.news-date{width:47px;background:var(--green);color:var(--white);text-align:center;padding-top:12px}
.news-date b{display:block;font-size:22px;line-height:24px}
.news-date small{font-size:9px;font-weight:700}
.news-body{padding:18px 16px 0 18px}
.news-body h4{font-size:13px;font-weight:400;color:#222;line-height:18px}
.news-body p{font-size:9.5px;line-height:15px;color:var(--muted);margin-top:8px}

/* blog */
.blog{top:1843px;height:286px}
.blog .head-row{top:52px}
.blog-list{position:absolute;left:132px;top:94px;width:936px;display:flex;justify-content:space-between}
.post{width:441px;display:flex;gap:14px}
.post-img{width:178px;height:129px;flex:none}
.post-date{font-size:12px;color:var(--blue)}
.post h4{font-size:15px;font-weight:400;color:#222;line-height:21px;margin-top:12px}
.post p{font-size:9.5px;line-height:14px;color:var(--muted);margin-top:12px}

/* footer */
.site-footer{top:2129px;height:175px;background:var(--footer);color:#aaa;font-size:10.5px}
.footer-cols{position:absolute;left:132px;top:30px;width:936px;display:flex}
.fcol{border-right:1px solid #3d3d3d;height:115px;padding-right:18px}
.fcol:last-child{border:0}
.fcol h5{font-size:12px;font-weight:400;color:var(--blue);margin-bottom:12px}
.fcol li{list-style:none;line-height:19px}
.fcol li::before{content:"› ";color:#777}
.fcol .line{line-height:19px}
.subscribe{display:flex;margin-top:4px}
.subscribe span{width:192px;height:36px;background:var(--white);color:#555;font-size:10px;line-height:36px;padding-left:14px}
.subscribe i{width:26px;height:36px;background:var(--blue);display:block}
.social{display:flex;gap:8px;justify-content:flex-end}
.social span{width:26px;height:26px;border-radius:50%;border:1px solid #ccc}
.copyright{top:2304px;height:58px;background:var(--footer-deep);color:#999;font-size:10.5px;text-align:center;line-height:58px}
</style>
</head>
<body>

<header class="site-header">
  <div class="brand"><span class="brand-dot"></span><span class="brand-name">VANTAGE TRAIL LABS</span></div>
  <div class="call">
    <div><div class="call-label">Call us on</div><div class="call-number">555 010 2244</div></div>
    <div class="call-icon"><svg width="14" height="14" viewBox="0 0 24 24"><path fill="#fff" d="M6.6 10.8a15 15 0 0 0 6.6 6.6l2.2-2.2c.3-.3.7-.4 1-.2 1.1.4 2.3.6 3.6.6.6 0 1 .4 1 1V20c0 .6-.4 1-1 1A17 17 0 0 1 3 4c0-.6.4-1 1-1h3.5c.6 0 1 .4 1 1 0 1.3.2 2.5.6 3.6.1.3 0 .7-.2 1z"/></svg></div>
  </div>
  <nav class="nav"><span class="active">Home</span><span>About Us</span><span>Services</span><span>Projects</span><span>Contact us</span></nav>
</header>

<section class="hero" role="img" aria-label="Business person holding a laptop beside a sketched globe with world landmarks on a concrete wall">
  <h1 class="hero-title">Phasellus purus non<br>neque ultricies bibendum</h1>
  <span class="hero-arrow left"><svg width="8" height="12"><path d="M7 1 2 6l5 5" stroke="#fff" fill="none" stroke-width="1.5"/></svg></span>
  <span class="hero-arrow right"><svg width="8" height="12"><path d="M1 1l5 5-5 5" stroke="#fff" fill="none" stroke-width="1.5"/></svg></span>
</section>

<section class="welcome">
  <h2 class="section-title">Welcome to Vantage Trail Labs</h2>
  <p>Mauris et euismod lacus. Donec faucibus felis nisi, ac gravida metus aliquam sit amet. Cras id pellentesque dui, vitae mollis lacus. Curabitur magna orci, vehicula nec semper ut, vestibulum eget mi. In in tempus felis. Ut porta, ante nec finibus lobortis, diam metus malesuada metus, nec pellentesque felis eros id ligula. Phasellus et fringilla tellus. Suspendisse ut libero quis leo posuere malesuada nec non nulla. Nulla molestie arcu quis elit convallis, eget viverra enim convallis. Mauris et euismod lacus. Donec faucibus felis nisi, ac gravida metus aliquam sit amet. Cras id pellentesque dui, vitae mollis lacus. Curabitur magna orci, vehicula nec semper ut.</p>
</section>

<section class="services">
  <h2 class="section-title">Our Services</h2>
  <div class="service-list">
    <div class="service">
      <div class="service-icon"><svg width="26" height="22"><g fill="none" stroke="#fff" stroke-width="2"><path d="M2 1v19h23"/><path d="M7 17V11M12 17V7M17 17V9M22 17V5"/></g></svg></div>
      <h3>Nunc sapien neque</h3>
      <p>Etiam hendrerit ante et sem bibendum blandit. Sed varius hendrerit lacinia. Integer dignissim placerat diam, vel dapibus urna facilisis eget.</p>
      <span class="btn">Learn more</span>
    </div>
    <div class="service">
      <div class="service-icon"><svg width="24" height="24"><circle cx="12" cy="12" r="10" fill="#fff"/></svg></div>
      <h3>Mauris et euismod lacus</h3>
      <p>Etiam hendrerit ante et sem bibendum blandit. Sed varius hendrerit lacinia. Integer dignissim placerat diam, vel dapibus urna facilisis eget.</p>
      <span class="btn">Learn more</span>
    </div>
    <div class="service">
      <div class="service-icon"><svg width="26" height="26"><circle cx="10" cy="15" r="6" fill="none" stroke="#fff" stroke-width="3"/><circle cx="19" cy="7" r="4" fill="none" stroke="#fff" stroke-width="2.5"/></svg></div>
      <h3>Phasellus eu purus</h3>
      <p>Etiam hendrerit ante et sem bibendum blandit. Sed varius hendrerit lacinia. Integer dignissim placerat diam, vel dapibus urna facilisis eget.</p>
      <span class="btn">Learn more</span>
    </div>
  </div>
</section>

<section class="projects">
  <div class="head-row"><h2 class="section-title">Our Projects</h2><div class="pager"><span></span><span class="on"><svg width="6" height="8"><path d="M1 1l4 3-4 3" stroke="#fff" fill="none"/></svg></span></div></div>
  <div class="project-list">
    <article class="project"><div class="project-img" role="img" aria-label="Hand holding a small toy plane against a bright sky" style="background:linear-gradient(180deg,#7fb0d8,#e9d9b8)"></div><h4>Donec non mauris tellus. Nunc ac felis ac quam dictum sagittis.</h4><p>Sed varius hendrerit lacinia. Integer dignissim placerat diam, vel dapibus urna facilisis eget. Fusce placerat lectus quis nisi. <span class="more">More</span></p></article>
    <article class="project"><div class="project-img" role="img" aria-label="Laptop on a wooden desk with a world map graphic" style="background:linear-gradient(180deg,#4a86b8,#6b5440)"></div><h4>Proin fermentum lorem mollis laoreet volutpat.</h4><p>Sed varius hendrerit lacinia. Integer dignissim placerat diam, vel dapibus urna facilisis eget. Fusce placerat lectus quis nisi. <span class="more">More</span></p></article>
    <article class="project"><div class="project-img" role="img" aria-label="Plane flying over the sea at sunset" style="background:linear-gradient(180deg,#4d6f9e,#d99a5c 70%,#2d4868)"></div><h4>Mauris pulvinar mattis nulla, vitae tincidunt ipsum</h4><p>Sed varius hendrerit lacinia. Integer dignissim placerat diam, vel dapibus urna facilisis eget. Fusce placerat lectus quis nisi. <span class="more">More</span></p></article>
    <article class="project"><div class="project-img" role="img" aria-label="Business person with a glowing world map of travel icons" style="background:linear-gradient(180deg,#2a6fa8,#1a1f2a)"></div><h4>Aenean varius rutrum mauris sed laoreet</h4><p>Sed varius hendrerit lacinia. Integer dignissim placerat diam, vel dapibus urna facilisis eget. Fusce placerat lectus quis nisi. <span class="more">More</span></p></article>
  </div>
</section>

<section class="news">
  <div class="head-row"><h2 class="section-title">Latest News</h2><span class="view-all">View All</span></div>
  <div class="news-list">
    <article class="news-card"><div class="news-date"><b>23</b><small>AUG</small></div><div class="news-body"><h4>Praesent magna eros, finibus vitae tincidunt vel, gravida ut erat</h4><p>Curabitur posuere tortor eget cursus molestie. Nunc lobortis gravida leo a maximus. In luctus sem in dui porta, eu dapibus leo viverra. Nam gravida quam. <span class="more">More</span></p></div></article>
    <article class="news-card"><div class="news-date"><b>23</b><small>AUG</small></div><div class="news-body"><h4>Praesent magna eros, finibus vitae tincidunt vel, gravida ut erat</h4><p>Curabitur posuere tortor eget cursus molestie. Nunc lobortis gravida leo a maximus. In luctus sem in dui porta, eu dapibus leo viverra. Nam gravida quam. <span class="more">More</span></p></div></article>
    <article class="news-card"><div class="news-date"><b>23</b><small>AUG</small></div><div class="news-body"><h4>Praesent magna eros, finibus vitae tincidunt vel, gravida ut erat</h4><p>Curabitur posuere tortor eget cursus molestie. Nunc lobortis gravida leo a maximus. In luctus sem in dui porta, eu dapibus leo viverra. Nam gravida quam. <span class="more">More</span></p></div></article>
  </div>
</section>

<section class="blog">
  <div class="head-row"><h2 class="section-title">Blog</h2><div class="pager"><span></span><span class="on"><svg width="6" height="8"><path d="M1 1l4 3-4 3" stroke="#fff" fill="none"/></svg></span></div></div>
  <div class="blog-list">
    <article class="post"><div class="post-img" role="img" aria-label="Moving walkway inside a modern terminal" style="background:linear-gradient(180deg,#9aa6a8,#5e6a5a)"></div><div><div class="post-date">18 August, 2016</div><h4>Donec ultrices in lorem eu dignissim. Suspendisse tortor urna, lacinia et aliquam nec, aliquet et.</h4><p>Proin porta fermentum ipsum, vel porttitor turpis venenatis luctus. Vivamus volutpat eu sapien quis tempus. <span style="color:#222">More</span></p></div></article>
    <article class="post"><div class="post-img" role="img" aria-label="Traveller seated in a private jet cabin" style="background:linear-gradient(180deg,#6b5a4a,#d8cbb8)"></div><div><div class="post-date">18 August, 2016</div><h4>Donec ultrices in lorem eu dignissim. Suspendisse tortor urna, lacinia et aliquam nec, aliquet et.</h4><p>Proin porta fermentum ipsum, vel porttitor turpis venenatis luctus. Vivamus volutpat eu sapien quis tempus. <span style="color:#222">More</span></p></div></article>
  </div>
</section>

<footer class="site-footer">
  <div class="footer-cols">
    <div class="fcol" style="width:100px"><h5>Links</h5><ul><li>Home</li><li>About Us</li><li>Services</li><li>Projects</li><li>Contact us</li></ul></div>
    <div class="fcol" style="width:286px;padding-left:18px"><h5>Contact Info</h5><div class="line">28 Building name, Street name, City - Zipcode</div><div class="line">Phone : 555 010 2244</div><div class="line">Fax : 555 010 2245</div><div class="line">Email : hello@vantagetrail.example</div></div>
    <div class="fcol" style="width:152px;padding-left:18px"><h5>Support</h5><ul><li>Terms of Use</li><li>Privacy Policy</li><li>Affiliate Disclosure</li><li>Attributions</li></ul></div>
    <div class="fcol" style="width:290px;padding-left:36px"><h5>Newsletter Subscribe</h5><div class="subscribe"><span>Email Address</span><i></i></div></div>
    <div class="fcol" style="width:108px;text-align:right"><h5>Connect with us</h5><div class="social"><span></span><span></span><span></span></div></div>
  </div>
</footer>
<footer class="copyright">Copyright © 2016 Vantage Trail Labs. All rights reserved.</footer>

</body>
</html>
```